Banner poster with different motifs

I'm looking for 5 banners and posters in A1 format in the same design, or the similarity must be recognizable...
Kept quite simple with different titles.

1 ballet
2 Contemporary Dance
3 high heels
4 Salsa & Bachata & Zouk
5 Hip Hop

Modern bright colors
it is for the entrance so that the students see here is a dance school

The text may also be included in the image
The photos are for guidance only; some are our own, some are purchased. However, we are permitted to use them, including our logo, of course.

```html
<!DOCTYPE html>
<html lang="en">
<head>
<meta charset="utf-8">
<title>Solvia Dance Center – Ballet Poster</title>
<link rel="stylesheet" href="https://fonts.googleapis.com/css2?family=Josefin+Sans:wght@300;400&family=Montserrat:wght@300;400&display=swap">
<style>
  :root {
    --stage: #ececec;
    --paper: #ffffff;
    --ink: #1c1c1c;
    --ink-soft: #3a3a3a;
    --photo-skin: #e6d6c6;
    --photo-cream: #efe6dc;
    --photo-tutu: #f3f0ec;
    --floor: #e7e2dc;
    --floor-warm: #ddd2c6;
  }
  * { margin: 0; padding: 0; box-sizing: border-box; }
  html, body {
    width: 1200px; height: 800px; overflow: hidden;
    background: var(--stage);
  }
  .canvas {
    width: 1200px; height: 800px;
    display: flex; align-items: center; justify-content: center;
  }
  .poster {
    position: relative;
    width: 537px; height: 760px;
    background: var(--paper);
    overflow: hidden;
    box-shadow: 0 2px 10px rgba(0,0,0,0.12);
    font-family: "Montserrat", sans-serif;
    color: var(--ink);
  }
  .poster__photo {
    position: absolute;
    left: 90px; top: 70px; width: 380px; height: 640px;
    border-radius: 190px 190px 24px 24px;
    background:
      radial-gradient(ellipse 40% 22% at 50% 46%, var(--photo-tutu) 0%, rgba(243,240,236,0) 100%),
      linear-gradient(180deg, var(--photo-cream) 0%, var(--photo-skin) 45%, var(--photo-cream) 75%, var(--floor-warm) 100%);
    opacity: 0.9;
  }
  .poster__floor {
    position: absolute; left: 0; right: 0; bottom: 0; height: 110px;
    background: linear-gradient(180deg, rgba(231,226,220,0) 0%, var(--floor) 55%, var(--floor-warm) 100%);
  }
  .brand {
    position: absolute; top: 34px; left: 0; right: 0;
    display: flex; flex-direction: column; align-items: center;
  }
  .brand__dot {
    width: 58px; height: 58px; border-radius: 50%;
    border: 1.5px solid var(--ink);
    background: var(--paper);
    margin-bottom: 8px;
  }
  .brand__name {
    font-family: "Josefin Sans", sans-serif;
    font-weight: 300; font-size: 36px; letter-spacing: 2px;
    line-height: 1;
  }
  .brand__tagline {
    font-family: "Josefin Sans", sans-serif;
    font-weight: 300; font-size: 10px; letter-spacing: 4px;
    margin-top: 6px;
  }
  .title {
    position: absolute; top: 418px; left: 0; right: 0;
    display: flex; flex-direction: column; align-items: center;
  }
  .title__word {
    font-family: "Josefin Sans", sans-serif;
    font-weight: 300; font-size: 74px; letter-spacing: 30px;
    padding-left: 30px; line-height: 1;
  }
  .title__label {
    margin-top: 10px;
    border: 1px solid var(--ink);
    background: rgba(255,255,255,0.55);
    padding: 4px 10px 2px;
    font-family: "Josefin Sans", sans-serif;
    font-weight: 300; font-size: 20px; letter-spacing: 0.5px;
  }
  .contact {
    position: absolute; left: 34px; right: 34px; bottom: 34px;
    display: flex; justify-content: space-between;
    font-size: 11px; font-weight: 300; color: var(--ink-soft);
    letter-spacing: 0.3px;
  }
</style>
</head>
<body>
<div class="canvas">
  <article class="poster">
    <div class="poster__photo" role="img" aria-label="Photograph of a ballerina in a white tutu posing en pointe against a bright white studio background"></div>
    <div class="poster__floor"></div>

    <header class="brand">
      <span class="brand__dot"></span>
      <span class="brand__name">SOLVIA</span>
      <span class="brand__tagline">DANCE CENTER FRANKFURT</span>
    </header>

    <div class="title">
      <h1 class="title__word">BALLET</h1>
      <span class="title__label">Solvia Dance Center</span>
    </div>

    <footer class="contact">
      <span class="contact__phone">+49(0) 170 555 018 42</span>
      <span class="contact__email">info@solvia-dance.de</span>
      <span class="contact__web">www.solvia-dance.de</span>
    </footer>
  </article>
</div>
</body>
</html>
```